New Service Brochure for The Brellford Spa

Hi All! We are looking for a new brochure design- tri-fold, double sided, and full color. We are a certified Tallow Spa for men and women in the heart of the Catskill Mountains of upstate New York. Our clients would describe us as laid back luxury with no pretensions and a home away from home vibe. Our font is Avalon. Key colors are black, white and gold. Looking for an inviting, clean, and modern/minimalist spread with a touch of elegance. No orchid imagery, please. I would like our "Tallow Spa" logo on cover, too please. Front cover image with with logo and "Tallow Spa" Sticker . Bottom of back with contact info. We would prefer massages go on left inside page, facials in middle and right inside, nails on back left, but we are open to new or different layout proposals. Thank you!

Target Market(s)

Men & Women.

Industry/Entity Type

Health And Wellness

Other font styles liked:
• Avalon is our signature font

Requirements
Must have
• Easy on the eyes.
Nice to have
• Negative space.
Should not have
• No orchids. Busy lines and wild colors.

```html
<!DOCTYPE html>
<html lang="en">
<head>
<meta charset="utf-8">
<title>The Brellford Spa – Service Brochure</title>
<link href="https://fonts.googleapis.com/css2?family=Cormorant+Garamond:wght@500;600&family=Great+Vibes&family=Open+Sans:wght@400;600;700&display=swap" rel="stylesheet">
<style>
:root{
  --gold:#c9a14a;
  --gold-dark:#a7802f;
  --ink:#1b1b1b;
  --char:#2a2826;
  --black:#111;
  --paper:#ffffff;
  --muted:#6d6a66;
  --light:#bdb8b0;
}
*{box-sizing:border-box;margin:0;padding:0}
html,body{width:778px;height:1200px;overflow:hidden;background:#fff}
body{position:relative;font-family:"Open Sans",Arial,sans-serif;color:var(--ink)}
.sheet{position:absolute;left:6px;width:766px;display:flex;box-shadow:0 1px 4px rgba(0,0,0,.25)}
.sheet--outside{top:6px;height:580px}
.sheet--inside{top:610px;height:584px}
.panel{position:relative;width:255.33px;height:100%;overflow:hidden}
.panel + .panel{border-left:1px solid rgba(0,0,0,.08)}
.photo{position:absolute;left:0;width:100%}
.script{font-family:"Great Vibes",cursive;color:var(--gold);font-weight:400}
.brand{font-family:"Cormorant Garamond",serif;font-weight:600;color:var(--ink);text-align:center;letter-spacing:.06em;line-height:1}
.brand small{display:block;font-size:.32em;letter-spacing:.12em}
.tagline{font-family:"Cormorant Garamond",serif;font-style:italic;font-size:11px;color:var(--muted);text-align:center}
.item{margin-bottom:7px}
.item h4{font-size:7.5px;font-weight:700;color:var(--gold);text-transform:uppercase;letter-spacing:.04em}
.item p{font-size:6.3px;line-height:1.4;color:var(--muted)}
.dark .item p{color:var(--light)}

/* outside – left */
.nails{background:var(--paper);padding:16px 16px}
.nails .script{font-size:22px}
.nails .mark{position:absolute;top:14px;right:16px;width:24px;height:30px;background:var(--gold)}
.nails .list{margin-top:16px}
.nails .photo{bottom:0;height:150px;background:linear-gradient(135deg,#e9dccb,#cbb49a 60%,#a88a6b)}

/* outside – middle */
.back{background:var(--paper)}
.back .photo{top:0;height:110px;background:linear-gradient(120deg,#3b3733,#7a6c5a 55%,#d8c7a8)}
.back .brand{position:absolute;top:130px;width:100%;font-size:34px}
.back .tagline{position:absolute;top:214px;width:100%}
.gift{position:absolute;top:240px;left:77px;width:100px;height:18px;background:var(--gold);color:#fff;font-size:7px;font-weight:700;letter-spacing:.08em;text-align:center;line-height:18px;text-transform:uppercase}
.contact{position:absolute;top:272px;width:100%;text-align:center;font-size:7.5px;line-height:1.6;color:var(--ink)}
.contact strong{font-size:9px}
.hours{position:absolute;top:385px;width:100%;text-align:center;font-size:7px;line-height:1.6;color:var(--muted)}
.hours h5{font-size:8px;color:var(--gold);letter-spacing:.1em}
.back .strip{position:absolute;bottom:0;left:0;width:100%;height:100px;background:linear-gradient(90deg,#efe6da,#d6c3a9)}

/* outside – right (cover) */
.cover{background:var(--paper)}
.cover .brand{position:absolute;top:24px;width:100%;font-size:32px}
.cover .tagline{position:absolute;top:104px;width:100%}
.cover .photo{top:128px;height:300px;background:linear-gradient(160deg,#8f7055,#d9bea0 50%,#f3e9dc)}
.badge{position:absolute;top:398px;right:16px;font-family:"Cormorant Garamond",serif;font-weight:600;font-size:13px;color:var(--ink);text-transform:uppercase;letter-spacing:.08em;white-space:nowrap}
.escape{position:absolute;top:448px;left:10px;right:10px;text-align:center;font-family:"Cormorant Garamond",serif;font-weight:600;font-size:15px;line-height:1.2;color:var(--ink);letter-spacing:.04em}
.web{position:absolute;top:500px;width:100%;text-align:center;font-size:7.5px;color:var(--gold);letter-spacing:.05em}

/* inside */
.dark{background:linear-gradient(180deg,#1a1918,#2d2b29)}
.massage{padding:18px 16px}
.massage .script{font-size:26px}
.massage .intro{font-size:6.3px;line-height:1.45;color:var(--light);margin:4px 0 12px}
.massage .photo{bottom:0;height:120px;background:linear-gradient(135deg,#7a5a40,#c79f7a 55%,#3a2a1e)}
.facial{background:linear-gradient(180deg,#fbf8f3,#f1ece4)}
.facial .photo{top:0;height:150px;background:linear-gradient(135deg,#f4e6d8,#e2c6ab 60%,#c8a384)}
.facial .body{position:absolute;top:160px;left:16px;right:16px}
.facial .script{font-size:26px}
.facial .intro{font-size:6.3px;line-height:1.45;color:var(--muted);margin:4px 0 12px}
.hair{padding:18px 16px}
.hair .script{font-size:24px;text-align:right}
.hair .intro{font-size:6.3px;line-height:1.45;color:var(--light);margin:6px 0 10px}
.prices{display:grid;grid-template-columns:1fr 1fr;column-gap:14px;font-size:7px;color:var(--light);line-height:1.75}
.prices div{display:flex;justify-content:space-between}
.prices b{color:var(--gold);font-weight:600}
.hair h4{font-size:7.5px;color:var(--gold);letter-spacing:.05em;margin-bottom:3px}
.hair .note{font-size:6.3px;line-height:1.45;color:var(--light);margin-top:14px}
.hair .photo{bottom:0;height:150px;background:linear-gradient(135deg,#2b211a,#8a5a2e 50%,#d69a4c)}
</style>
</head>
<body>

<section class="sheet sheet--outside">
  <div class="panel nails">
    <h2 class="script">Hands &amp; Feet</h2>
    <div class="mark" role="img" aria-label="Spa emblem placeholder"></div>
    <div class="list">
      <div class="item"><h4>Classic Spa Manicure – $28</h4><p>Shape, buff and polish with a warm soak and soothing hand massage to finish.</p></div>
      <div class="item"><h4>Paraffin Manicure – $38</h4><p>Our classic manicure plus a warm paraffin wrap that softens dry, tired hands.</p></div>
      <div class="item"><h4>Classic Spa Pedicure – $45</h4><p>A relaxing foot soak, gentle scrub, nail care and polish for refreshed feet.</p></div>
      <div class="item"><h4>Mountain Pedicure – $60</h4><p>Exfoliating sugar scrub, cooling mask and extended massage of the lower legs.</p></div>
      <div class="item"><h4>Gentleman's Hand &amp; Foot – $55</h4><p>Clean nail grooming, cuticle care and buffing with a light conditioning balm.</p></div>
      <div class="item"><h4>Polish Change – $15</h4><p>Fresh color for hands or feet, with a quick file and glossy top coat.</p></div>
      <div class="item"><h4>Nail Art &amp; Add-ons – from $5</h4><p>Simple accents, French tips or extra massage time added to any service.</p></div>
    </div>
    <div class="photo" role="img" aria-label="Photo of feet resting during a pedicure"></div>
  </div>

  <div class="panel back">
    <div class="photo" role="img" aria-label="Photo of candles and smooth spa stones"></div>
    <h1 class="brand">THE<br>BRELLFORD<br><small>SPA</small></h1>
    <p class="tagline">a boutique spa for Men &amp; Women</p>
    <div class="gift">Gift Certificates</div>
    <div class="contact">
      <strong>(518) 555-0142</strong><br>
      info@thebrellfordspa.com<br>
      22 Larkfield Hollow Road<br>
      Brellford, NY 12400<br>
      Just off Main Street
    </div>
    <div class="hours">
      <h5>HOURS</h5>
      Thurs–Sat · 10am–6pm<br>
      Sun–Mon · 10am–5pm<br>
      Tues &amp; Wed · Closed
    </div>
    <div class="strip" role="img" aria-label="Photo of folded towels and spa stones"></div>
  </div>

  <div class="panel cover">
    <h1 class="brand">THE<br>BRELLFORD<br><small>SPA</small></h1>
    <p class="tagline">a boutique spa for Men &amp; Women</p>
    <div class="photo" role="img" aria-label="Photo of a guest relaxing during a massage"></div>
    <p class="badge">Tallow Spa</p>
    <p class="escape">ESCAPE THE CONGESTION OF<br>EVERYDAY LIFE!</p>
    <p class="web">www.thebrellfordspa.com</p>
  </div>
</section>

<section class="sheet sheet--inside">
  <div class="panel dark massage">
    <h2 class="script">Massages</h2>
    <p class="intro">Relax, restore and unwind. Every massage is tailored to your needs, pressure and pace by our licensed therapists.</p>
    <div class="item"><h4>Swedish Massage – $85 / $120</h4><p>Long, flowing strokes ease tension and calm the mind for total relaxation.</p></div>
    <div class="item"><h4>Deep Tissue – $95 / $135</h4><p>Firm, focused pressure releases knots and chronic tightness in the muscles.</p></div>
    <div class="item"><h4>Hot Stone – $110</h4><p>Warm basalt stones melt away stress and deeply soothe tired muscles.</p></div>
    <div class="item"><h4>Couples Massage – $180</h4><p>Share a side-by-side session in our quiet room, perfect for two guests.</p></div>
    <div class="item"><h4>Prenatal Massage – $90</h4><p>Gentle, supported care designed for comfort during every stage of pregnancy.</p></div>
    <div class="item"><h4>Reflexology – $60</h4><p>Pressure on points of the feet and hands restores balance to the body.</p></div>
    <div class="item"><h4>Sports Massage – $95</h4><p>Stretching and targeted work that supports recovery after an active day.</p></div>
    <div class="photo" role="img" aria-label="Photo of a back massage"></div>
  </div>

  <div class="panel facial">
    <div class="photo" role="img" aria-label="Photo of a guest enjoying a facial treatment"></div>
    <div class="body">
      <h2 class="script">Facials</h2>
      <p class="intro">Each facial begins with a skin consultation so we can select products and steps that suit your skin today.</p>
      <div class="item"><h4>Signature Facial – $90</h4><p>Cleanse, exfoliate, extract and hydrate with a soothing mask and massage.</p></div>
      <div class="item"><h4>Gentleman's Facial – $85</h4><p>A deep clean that calms shaving irritation and refreshes tired skin.</p></div>
      <div class="item"><h4>Anti-Aging Facial – $115</h4><p>Firming serums and a lifting massage that smooth fine lines and restore glow.</p></div>
      <div class="item"><h4>Express Facial – $55</h4><p>A quick refresh for busy days, with cleansing, toning and moisture.</p></div>
      <div class="item"><h4>Teen Facial – $50</h4><p>Gentle care for young skin that clears pores and teaches healthy habits.</p></div>
    </div>
  </div>

  <div class="panel dark hair">
    <h2 class="script">Hair Removal</h2>
    <p class="intro">Smooth results with gentle warm wax, applied quickly and carefully for comfort in a private, relaxed setting.</p>
    <h4>WAXING</h4>
    <div class="prices">
      <div>Brow <b>$15</b></div><div>Bikini <b>$35</b></div>
      <div>Lip <b>$10</b></div><div>Chest <b>$45</b></div>
      <div>Chin <b>$12</b></div><div>Back <b>$55</b></div>
      <div>Full Face <b>$40</b></div><div>Underarm <b>$20</b></div>
      <div>Half Leg <b>$40</b></div><div>Arms <b>$35</b></div>
      <div>Full Leg <b>$70</b></div><div>Hands <b>$10</b></div>
    </div>
    <p class="note">Please arrive ten minutes early. Hair should be at least a quarter inch long for best results.</p>
    <div class="photo" role="img" aria-label="Photo of candles, oranges and spa stones"></div>
  </div>
</section>

</body>
</html>
```